Redesign of business card for Cedar Ridge Mechanical

We are looking for a new design for our business cards for Cedar Ridge Mechanical. We are a plumbing & HVAC construction company, operating on the West Coast of Canada and USA. Logo attached.
Industry/Entity Type
Construction - Plumbing & HVAC
Contact Information for Business Card
Name, address, phone numbers, email, website address
Look and feel
Each slider illustrates characteristics of the customer's brand and the style your logo design should communicate.

```html
<!DOCTYPE html>
<html lang="en">
<head>
<meta charset="utf-8">
<title>Cedar Ridge Mechanical – Business Card</title>
<link href="https://fonts.googleapis.com/css2?family=Montserrat:wght@400;500;700&display=swap" rel="stylesheet">
<style>
  :root {
    --page-bg: #d9d2c8;
    --card-bg: #ece6dd;
    --ink: #1b1b1b;
    --ink-soft: #2a2a2a;
    --silver: #9a948c;
    --silver-light: #e4ded5;
  }
  * { margin: 0; padding: 0; box-sizing: border-box; }
  html, body {
    width: 1200px;
    height: 1047px;
    overflow: hidden;
    background: var(--page-bg);
    font-family: "Montserrat", sans-serif;
    color: var(--ink);
  }
  .business-card {
    position: absolute;
    left: 80px;
    top: 233px;
    width: 1040px;
    height: 580px;
    background: var(--card-bg);
    border-radius: 26px;
    overflow: hidden;
    box-shadow: 0 10px 30px rgba(0,0,0,0.12);
  }
  .brand-mark {
    position: absolute;
    left: 47px;
    top: 52px;
    display: flex;
    align-items: center;
    gap: 16px;
  }
  .brand-square {
    width: 34px;
    height: 34px;
    background: var(--ink);
  }
  .brand-name {
    font-weight: 700;
    font-size: 30px;
    line-height: 1.1;
    letter-spacing: 1px;
    text-transform: uppercase;
    color: var(--ink);
  }
  .holder {
    position: absolute;
    right: 50px;
    top: 57px;
    text-align: right;
  }
  .holder-name {
    font-weight: 700;
    font-size: 33px;
    letter-spacing: 1px;
  }
  .holder-title {
    font-weight: 500;
    font-size: 25px;
    color: var(--ink-soft);
    margin-top: 2px;
  }
  .accent-bar {
    position: absolute;
    right: 5px;
    top: 50px;
    width: 29px;
    height: 65px;
    background: var(--ink);
  }
  .address {
    position: absolute;
    left: 44px;
    top: 228px;
    font-size: 26px;
    line-height: 37px;
    color: var(--ink-soft);
  }
  .contact-list {
    position: absolute;
    left: 44px;
    top: 326px;
    list-style: none;
  }
  .contact-list li {
    display: flex;
    align-items: center;
    gap: 12px;
    font-size: 25px;
    height: 36px;
    color: var(--ink-soft);
  }
  .contact-list svg { width: 22px; height: 22px; fill: var(--ink-soft); }
  .brand-feature {
    position: absolute;
    right: 40px;
    top: 330px;
    text-align: right;
    font-weight: 700;
    font-size: 44px;
    line-height: 1.08;
    letter-spacing: 1px;
    text-transform: uppercase;
    color: var(--ink);
  }
  .card-wave {
    position: absolute;
    left: 0;
    bottom: 0;
    width: 1040px;
    height: 580px;
  }
</style>
</head>
<body>
  <div class="business-card">
    <svg class="card-wave" viewBox="0 0 1040 580" preserveAspectRatio="none" aria-hidden="true">
      <defs>
        <linearGradient id="silverSwoosh" x1="0" y1="0" x2="1" y2="0">
          <stop offset="0" stop-color="#6f6a64"/>
          <stop offset="0.6" stop-color="#b8b1a8"/>
          <stop offset="1" stop-color="#e4ded5"/>
        </linearGradient>
      </defs>
      <path d="M0 420 C 150 450, 330 500, 520 478 C 360 500, 160 480, 0 452 Z" fill="url(#silverSwoosh)"/>
      <path d="M0 488 C 140 520, 260 535, 380 522 C 500 508, 600 470, 680 455 L 1040 455 L 1040 580 L 0 580 Z" fill="var(--ink)"/>
    </svg>

    <div class="brand-mark">
      <div class="brand-square"></div>
      <div class="brand-name">Cedar Ridge<br>Mechanical</div>
    </div>

    <div class="holder">
      <div class="holder-name">DANIEL HART</div>
      <div class="holder-title">Managing Director</div>
    </div>
    <div class="accent-bar"></div>

    <div class="address">Your address, City<br>State, Zip 1234</div>

    <ul class="contact-list">
      <li>
        <svg viewBox="0 0 24 24"><path d="M6.6 10.8a15.1 15.1 0 0 0 6.6 6.6l2.2-2.2a1 1 0 0 1 1-.25 11.4 11.4 0 0 0 3.6.57 1 1 0 0 1 1 1V20a1 1 0 0 1-1 1A17 17 0 0 1 3 4a1 1 0 0 1 1-1h3.5a1 1 0 0 1 1 1c0 1.25.2 2.45.57 3.57a1 1 0 0 1-.25 1z"/></svg>
        123 456 789
      </li>
      <li>
        <svg viewBox="0 0 24 24"><path d="M3 6h18v12H3z M3 6l9 7 9-7" fill="none" stroke="#2a2a2a" stroke-width="2"/></svg>
        info@yourmail.com
      </li>
      <li>
        <svg viewBox="0 0 24 24"><circle cx="12" cy="12" r="10"/></svg>
        www.yourwebsite.com
      </li>
    </ul>

    <div class="brand-feature">Cedar Ridge<br>Mechanical</div>
  </div>
</body>
</html>
```